Events Company Needs Website Revamp

Tallwood Expos is an events company that specializes in organizing and marketing large scale consumer and trade events globally.

The new web design should provide easy classification of the events, and allow visitors to find and access the details page within 2 clicks.

There are no strict guidelines on the color theme. It just has to blend naturally with the corporate logo.
Updates

The company logo is uploaded (pdf & ai)

I came across this design which I like very much. Elegant and corporate with nice modern fonttype.

Layout wise, neat and clear. 

Please see how you can emulate the design further. Particularly, highlighting the 2 event arms (Trade/Consumer) clearly.

Target Market(s)

Consumer looking for upcoming events, B2C companies looking to participate, B2B companies looking to connect with other companies

Industry/Entity Type

It Company

Requirements
Must have
• The new design should help to achieve the following objectives:
1) Visitors should be able to easily identify and access the 2 different types of events (i.e. Trade Events and Consumer Events).
2) Visitors should be able to easily find events that interest them (e.g. filter by date, trade or consumer, category [i.e. beauty, retail, F&B, construction, etc.]).
3) Visitors should be able to access an event’s details page within 2 clicks from any page.

Main navigation to include the following links:
- About Us
- Calendar
- Consumer Events
- Trade Events
- Contact Us

Design for Three (3) pages required:
A. Homepage
- Clear differentiation and easy access to the 2 different types of events (trade and consumer)
- Featured area to showcase latest 4-5 events
- Quick way to access events calendar
- Clear call-to-action for newsletter signup
- Social media sharing widgets/buttons
- A section for latest news and press releases
- A section for featured testimonials

B. Events Listing Page
- List of links to all events
- Logos and/or photos of events
- Filter / tags to find events in a specific category (e.g. food, electronics, building & construction, etc.)

C. Events Details Page
- Photo strip to showcase event photos / brochure
- A section with event details (Date, Venue, Event Description, etc.)
- Call-to-action button to visit event website
- Call-to-action button to contact event sales team
- E.g. http://vantly-demo.com/user/brightfoxhk/brightfox-monday-2011 but with the photo strip permanently extended and of a shorter height. Event details and call-to-action buttons should also be easily seen

```html
<!DOCTYPE html>
<html lang="en">
<head>
<meta charset="utf-8">
<title>Tallwood Expos – Home</title>
<link rel="stylesheet" href="https://fonts.googleapis.com/css2?family=Open+Sans:wght@400;600;700&display=swap">
<style>
:root{
  --orange:#f7801e;
  --orange-dark:#e8650a;
  --blue:#1667b8;
  --blue-dark:#0d4f96;
  --green:#6aaa1d;
  --green-dark:#4f8a10;
  --red:#e0261c;
  --red-dark:#b81a12;
  --text:#555;
  --heading:#222;
  --panel:#f3f3f3;
  --border:#dcdcdc;
  --footer:#e2e2e2;
}
*{box-sizing:border-box;margin:0;padding:0}
html,body{width:740px;height:1200px;overflow:hidden;background:#fff}
body{position:relative;font-family:"Open Sans",Arial,sans-serif;color:var(--text);font-size:8px;line-height:1.4}
.abs{position:absolute}

/* header */
.social-bar{left:464px;top:0;width:207px;height:18px;background:linear-gradient(#f4f4f4,#d8d8d8);border-radius:0 0 4px 4px;display:flex;align-items:center;justify-content:space-around;font-size:8px;color:#444}
.social-bar span{display:flex;align-items:center;gap:4px}
.social-bar i{width:9px;height:9px;background:#8aa0b8;display:block}
.brand{left:68px;top:30px;white-space:nowrap}
.brand-name{display:flex;align-items:center;gap:5px;font-size:17px;font-weight:700;color:#333;line-height:1}
.brand-name i{width:22px;height:22px;border-radius:50%;background:var(--orange);display:block}
.brand-sub{margin-top:32px;margin-left:12px;font-size:5.5px;color:var(--blue);letter-spacing:.2px}
.call{left:308px;top:42px;display:flex;gap:6px;color:var(--red);font-size:10.5px;line-height:1.45}
.search{left:496px;top:47px;width:175px;height:20px;border:1px solid #bbb;border-radius:10px;overflow:hidden;display:flex}
.search span{flex:1;padding:4px 8px;font-size:7px;color:#888}
.search b{width:25px;background:var(--green);display:flex;align-items:center;justify-content:center}

/* nav */
.main-nav{left:68px;top:95px;width:602px;height:25px;display:flex;background:var(--orange)}
.main-nav a{color:#fff;text-decoration:none;font-size:9.5px;display:flex;align-items:center;justify-content:center;border-right:1px solid #fba259;background:linear-gradient(#fa9a3c,var(--orange-dark))}
.main-nav a.current{background:linear-gradient(#2a7fd0,var(--blue-dark))}

/* slider */
.slider{left:68px;top:133px;width:602px;height:212px;border:1px solid var(--border);border-radius:3px;background:#fff}
.slide{position:absolute;left:8px;top:7px;width:584px;height:193px;background:linear-gradient(120deg,#7a1a3c,#c8507a 35%,#4a78a8 60%,#6a3858)}
.slider-arrow{position:absolute;top:95px;width:19px;height:19px;border-radius:50%;background:#111;display:flex;align-items:center;justify-content:center}

/* finder */
.finder-tab{left:68px;top:358px;width:132px;height:19px;background:var(--green);clip-path:polygon(0 0,82% 0,100% 100%,0 100%);color:#fff;font-size:8.5px;font-weight:700;padding:4px 10px}
.finder{left:68px;top:377px;width:602px;height:55px;background:linear-gradient(#f8f8f8,#ececec);border:1px solid var(--border)}
.finder label{position:absolute;top:11px;font-size:7.5px;color:#555}
.select{position:absolute;top:25px;height:17px;border:1px solid #c8c8c8;border-radius:3px;background:#fff}
.select::after{content:"";position:absolute;right:0;top:0;width:13px;height:15px;background:var(--green)}
.filter-btn{position:absolute;left:542px;top:25px;width:51px;height:17px;border-radius:3px;background:linear-gradient(#8cd03a,var(--green-dark));color:#2f5a05;font-size:9px;font-weight:700;display:flex;align-items:center;justify-content:center}

/* event arms */
.arm{top:447px;width:295px;height:134px;border:1px solid var(--border);border-radius:3px;background:#fff}
.arm h2{height:18px;background:var(--orange);color:#fff;font-size:8.5px;font-weight:700;padding:3px 10px;border-radius:3px 3px 0 0}
.arm-photo{position:absolute;left:10px;top:28px;width:85px;height:95px;border:1px solid #ccc}
.arm p{position:absolute;left:108px;top:25px;width:177px;font-size:7px;line-height:1.6}
.view-more{position:absolute;left:228px;top:107px;width:57px;height:17px;background:var(--orange);clip-path:polygon(0 0,88% 0,100% 50%,88% 100%,0 100%);color:#fff;font-size:6.5px;display:flex;align-items:center;justify-content:center}

/* category cards */
.cat{top:594px;width:141px;height:161px}
.cat h3{width:107px;height:15px;background:var(--blue);clip-path:polygon(0 0,100% 0,93% 100%,0 100%);color:#fff;font-size:8px;font-weight:700;padding:2px 9px;letter-spacing:.3px}
.cat-body{position:absolute;top:15px;left:0;width:141px;height:146px;background:var(--panel);border:1px solid var(--border);border-top:none}
.cat-photo{position:absolute;left:9px;top:13px;width:122px;height:64px;border:1px solid #ccc}
.cat p{position:absolute;left:9px;top:84px;width:116px;font-size:7px;line-height:1.55}
.learn{position:absolute;right:13px;top:129px;font-size:6.5px;color:var(--red);text-decoration:underline}

/* lower row */
.box{top:770px;height:250px;background:var(--panel);border:1px solid var(--border);border-radius:3px}
.box h2{width:182px;height:22px;background:var(--red);clip-path:polygon(0 0,80% 0,100% 30%,100% 100%,0 100%);color:#fff;font-size:9px;font-weight:600;letter-spacing:.5px;padding:5px 8px}
.news-item{position:absolute;left:8px;width:230px;height:52px}
.news-photo{position:absolute;left:0;top:0;width:53px;height:52px;border:1px solid #999;background:linear-gradient(135deg,#5a3a8a,#c86aa8 55%,#3a4a8a)}
.news-item b{position:absolute;left:63px;top:0;font-size:7.5px;color:var(--heading);font-weight:600}
.news-item span{position:absolute;left:63px;top:10px;width:165px;font-size:6.5px;line-height:1.4}
.more{position:absolute;top:223px;font-size:7px;color:var(--red)}
.more::after{content:" ▸";color:#333}
.quote{position:absolute;left:9px;top:38px;width:147px;font-size:6.8px;line-height:1.67;text-align:justify}

.calendar-box{left:505px;top:771px;width:165px;height:176px;background:var(--panel);border:1px solid var(--border);border-radius:3px}
.calendar-box h2{position:absolute;left:9px;top:5px;font-size:8.5px;color:var(--green-dark);font-weight:700;letter-spacing:.5px}
.cal{position:absolute;left:9px;top:26px;width:146px;background:#fff;border:1px solid #ccc}
.cal-head{height:23px;background:linear-gradient(#d23a1c,var(--red-dark));color:#fff;font-size:8.5px;display:flex;align-items:center;justify-content:space-between;padding:0 6px}
.cal table{width:100%;border-collapse:collapse;table-layout:fixed}
.cal th{font-size:6.5px;font-weight:400;color:#555;height:13px}
.cal td{height:21px;border:1px solid #ddd;text-align:center;font-size:9.5px;color:#222}
.cal td.today{background:var(--red-dark);color:#fff}
.cal td.soft{background:#e6e6e6;color:#888}

.newsletter{left:505px;top:955px;width:165px;height:65px;background:var(--green);border-radius:3px}
.newsletter h2{position:absolute;left:40px;top:6px;color:#fff;font-size:10.5px;font-weight:700}
.news-icon{position:absolute;left:9px;top:3px;width:24px;height:20px}
.news-input{position:absolute;left:9px;top:27px;width:146px;height:22px;background:#fff;border-radius:3px;font-size:6.5px;color:#777;padding:6px 7px}
.news-btn{position:absolute;left:109px;top:27px;width:46px;height:22px;background:linear-gradient(#ec3b2c,var(--red-dark));border-radius:3px;color:#fff;font-size:9px;display:flex;align-items:center;justify-content:center}

/* footer */
.footer{left:0;top:1045px;width:740px;height:155px;background:var(--footer)}
.footer-col{position:absolute;top:18px;font-size:6.8px;color:#444;line-height:2}
.footer-col h4{font-size:8.5px;color:var(--heading);font-weight:700;margin-bottom:4px;letter-spacing:.3px}
.social-icons{display:flex;gap:3px}
.social-icons i{width:21px;height:21px;border-radius:3px;display:block}
.footer-rule{position:absolute;left:68px;top:124px;width:602px;border-top:1px dotted #888}
.copyright{position:absolute;left:0;top:130px;width:740px;text-align:center;font-size:7px;color:#444}
</style>
</head>
<body>

<header>
  <div class="abs social-bar"><span><i></i>Follow us on Chirper</span><span><i></i>Join us on Facepage</span></div>
  <div class="abs brand">
    <div class="brand-name"><i></i>Tallwood Expos</div>
    <div class="brand-sub">A SUBSIDIARY OF Norlane</div>
  </div>
  <div class="abs call">
    <svg width="20" height="20" viewBox="0 0 20 20"><circle cx="10" cy="6" r="4" fill="#555"/><path d="M2 20c0-5 3.5-8 8-8s8 3 8 8z" fill="#333"/><path d="M9 12h2l-1 6z" fill="#c22"/></svg>
    <div>Call Now!<br>555 0142 7731</div>
  </div>
  <div class="abs search"><span>Search..</span><b><svg width="11" height="11" viewBox="0 0 11 11"><circle cx="4.5" cy="4.5" r="3.3" fill="none" stroke="#1a3a05" stroke-width="1.6"/><path d="M7 7l3 3" stroke="#1a3a05" stroke-width="1.8"/></svg></b></div>
</header>

<nav class="abs main-nav">
  <a class="current" style="width:78px">Home</a>
  <a style="width:91px">About Us</a>
  <a style="width:86px">Calendar</a>
  <a style="width:135px">Consumer Events</a>
  <a style="width:109px">Trade Events</a>
  <a style="width:103px;border-right:none">Contact Us</a>
</nav>

<section class="abs slider">
  <div class="slide" role="img" aria-label="Crowd of young people celebrating at a nightlife event"></div>
  <div class="slider-arrow" style="left:16px"><svg width="8" height="8" viewBox="0 0 8 8"><path d="M5.5 1L2.5 4l3 3" stroke="#fff" stroke-width="1.5" fill="none"/></svg></div>
  <div class="slider-arrow" style="left:566px"><svg width="8" height="8" viewBox="0 0 8 8"><path d="M2.5 1l3 3-3 3" stroke="#fff" stroke-width="1.5" fill="none"/></svg></div>
</section>

<section>
  <div class="abs finder-tab">FIND EVENTS</div>
  <div class="abs finder">
    <label style="left:9px">DATE</label>
    <label style="left:125px">TRADE &amp; CONSUMER</label>
    <label style="left:241px">CATEGORY</label>
    <label style="left:389px">ALL EVENTS</label>
    <div class="select" style="left:9px;width:105px"></div>
    <div class="select" style="left:125px;width:105px"></div>
    <div class="select" style="left:241px;width:136px"></div>
    <div class="select" style="left:389px;width:141px"></div>
    <div class="filter-btn">Filter&nbsp;<svg width="8" height="8" viewBox="0 0 11 11"><circle cx="4.5" cy="4.5" r="3.3" fill="none" stroke="#2f5a05" stroke-width="1.6"/><path d="M7 7l3 3" stroke="#2f5a05" stroke-width="1.8"/></svg></div>
  </div>
</section>

<section>
  <article class="abs arm" style="left:68px">
    <h2>TRADE EVENTS</h2>
    <div class="arm-photo" role="img" aria-label="Business audience raising hands at a trade conference" style="background:linear-gradient(160deg,#f0e6dc,#d8a080 55%,#c06040)"></div>
    <p>Contrary to popular belief, Lorem Ipsum is not simply random text. It has roots in a piece of classical Latin literature from 45 BC, making it over 2000 years old. There are many variations of passages of Lorem Ipsum available, but the majority have suffered alteration in some form, by injected humour, or randomised words believable...</p>
    <div class="view-more">View more</div>
  </article>
  <article class="abs arm" style="left:375px">
    <h2>CONSUMER EVENTS</h2>
    <div class="arm-photo" role="img" aria-label="Seated audience at a consumer show" style="background:linear-gradient(160deg,#2a3a5a,#7a5a50 55%,#3a2a2a)"></div>
    <p>Contrary to popular belief, Lorem Ipsum is not simply random text. It has roots in a piece of classical Latin literature from 45 BC, making it over 2000 years old. There are many variations of passages of Lorem Ipsum available, but the majority have suffered alteration in some form, by injected humour, or randomised words believable...</p>
    <div class="view-more">View more</div>
  </article>
</section>

<section>
  <article class="abs cat" style="left:68px">
    <h3>POPULAR EVENTS</h3>
    <div class="cat-body">
      <div class="cat-photo" role="img" aria-label="Performer on a purple lit stage" style="background:linear-gradient(120deg,#5a2a8a,#b070c8 50%,#3a1a6a)"></div>
      <p>Lorem Ipsum is simply dummy text of the printing and typesetting industry dummy text ever since the 1500s....</p>
      <span class="learn">Learn more</span>
    </div>
  </article>
  <article class="abs cat" style="left:221px">
    <h3>CULTURAL EVENTS</h3>
    <div class="cat-body">
      <div class="cat-photo" role="img" aria-label="Traditional dancers in costume" style="background:linear-gradient(120deg,#8a2a2a,#d8c8b8 50%,#6a1a1a)"></div>
      <p>Lorem Ipsum is simply dummy text of the printing and typesetting industry dummy text ever since the 1500s....</p>
      <span class="learn">Learn more</span>
    </div>
  </article>
  <article class="abs cat" style="left:374px">
    <h3>MUSICAL EVENTS</h3>
    <div class="cat-body">
      <div class="cat-photo" role="img" aria-label="Band performing on a blue lit stage" style="background:linear-gradient(120deg,#1a4a9a,#5a8ad8 50%,#1a2a4a)"></div>
      <p>Lorem Ipsum is simply dummy text of the printing and typesetting industry dummy text ever since the 1500s....</p>
      <span class="learn">Learn more</span>
    </div>
  </article>
  <article class="abs cat" style="left:528px">
    <h3>FASHION EVENTS</h3>
    <div class="cat-body">
      <div class="cat-photo" role="img" aria-label="Group of models at a fashion party" style="background:linear-gradient(120deg,#3a2a20,#c89878 50%,#5a3a2a)"></div>
      <p>Lorem Ipsum is simply dummy text of the printing and typesetting industry dummy text ever since the 1500s....</p>
      <span class="learn">Learn more</span>
    </div>
  </article>
</section>

<section>
  <div class="abs box" style="left:68px;width:249px">
    <h2>NEWS &amp; PRESS RELEASES</h2>
    <div class="news-item" style="top:39px"><div class="news-photo" role="img" aria-label="Party crowd"></div><b>dolor sit amet</b><span>Contrary to popular belief, Lorem Ipsum is not simply lorem random text.</span></div>
    <div class="news-item" style="top:105px"><div class="news-photo" role="img" aria-label="Party crowd"></div><b>dolor sit amet</b><span>Contrary to popular belief, Lorem Ipsum is not simply lorem random text.</span></div>
    <div class="news-item" style="top:171px"><div class="news-photo" role="img" aria-label="Party crowd"></div><b>dolor sit amet</b><span>Contrary to popular belief, Lorem Ipsum is not simply lorem random text.</span></div>
    <span class="more" style="left:187px">More News</span>
  </div>

  <div class="abs box" style="left:327px;width:166px">
    <h2 style="width:140px">TESTIMONIALS</h2>
    <p class="quote">"All the Lorem Ipsum generators on the Internet tend to repeat predefined chunks as necessary, making this the first true generator on the Internet. It uses a dictionary of over 200 Latin words, combined with a handful of model sentence structures, to generate Lorem Ipsum which looks reasonable and more recently with desktop publishing software like Foldwright LayoutDesk including versions of Lorem Ipsum. The generated Lorem Ipsum is to generate Lorem Ipsum which looks reasonable and more recently therefore always free from repetition, injected humour, or non-characteristic words etc."</p>
    <span class="more" style="left:82px">More Testimonials</span>
  </div>

  <div class="abs calendar-box">
    <h2>CALENDAR</h2>
    <div class="cal">
      <div class="cal-head"><span>&#10094;</span><span>MAY 2010</span><span>&#10095;</span></div>
      <table>
        <tr><th>SUN</th><th>MON</th><th>TUE</th><th>WED</th><th>THU</th><th>FRI</th><th>SAT</th></tr>
        <tr><td></td><td>1</td><td>2</td><td>3</td><td>4</td><td>5</td><td>6</td></tr>
        <tr><td>7</td><td>8</td><td>9</td><td>10</td><td>11</td><td class="soft">12</td><td>13</td></tr>
        <tr><td>14</td><td>15</td><td class="today">16</td><td>17</td><td>18</td><td>19</td><td>20</td></tr>
        <tr><td>21</td><td>22</td><td>23</td><td>24</td><td>25</td><td>26</td><td>27</td></tr>
        <tr><td>28</td><td>29</td><td>30</td><td>31</td><td></td><td></td><td></td></tr>
      </table>
    </div>
  </div>

  <div class="abs newsletter">
    <svg class="news-icon" viewBox="0 0 24 20"><rect x="2" y="4" width="16" height="14" fill="#fff" stroke="#2a6a8a"/><path d="M5 8h10M5 11h10M5 14h7" stroke="#6a9ab8"/><path d="M14 2l8 8-3 1-7-7z" fill="#2a7ab8"/></svg>
    <h2>Get Our Newsletter!</h2>
    <div class="news-input">Enter Your Email Address</div>
    <div class="news-btn">Sign up</div>
  </div>
</section>

<footer class="abs footer">
  <div class="footer-col" style="left:77px"><h4>QUICK LINKS</h4>Home<br>About Us<br>Calendar<br>Consumer Events<br>Trade Events</div>
  <div class="footer-col" style="left:230px"><h4>EVENTS</h4>Popular Events<br>Culture Events<br>Musical Events<br>Fashion Events<br>Corporate Events</div>
  <div class="footer-col" style="left:384px"><h4>SOCIAL MEDIA</h4>
    <div class="social-icons"><i style="background:#2a6ab8"></i><i style="background:#3a5a9a"></i><i style="background:#4aaee0"></i><i style="background:#1a6a9a"></i></div>
  </div>
  <div class="footer-col" style="left:537px;line-height:2"><h4>CONTACT US</h4>Lorem Ipsum is simply,<br>dummy text of the ring, and<br>typesetting industry.<br><br>Ph:- &nbsp;555 0142 7731</div>
  <div class="footer-rule"></div>
  <div class="copyright">Copyright© 2012 Tallwood Expos. All Right Reserved.</div>
</footer>

</body>
</html>
```